Fitness Equipment & Service

I want to make the card eye catching and fun. We are called Corvane Motion Limited and we are based in Wales. We sell, install and service all types of fitness equipment from Skipping ropes, right through the Dumbbells, Kettle bells and Barbells through to state of the art Treadmills, Running Machines and Strength Equipment. We also design and install changing room furniture and lockers.

TYPOGRAPHY
We would like to use Futrura. Futura has an appearance of efficiency and forwardness. The typeface is derived
from simple geometric forms (near-perfect circles, triangles and squares) and is based on strokes of
near-even weight, which are low in contrast. This is most visible in the almost perfectly round stroke of
the o, which is nonetheless slightly ovoid.
The lowercase has tall ascenders, which rise above the cap line. The uppercase
characters present proportions similar to those of classical Roman capitals.

TYPOGRAPHIC CONSIDERATIONS
No Strike though
No Horizontal Scaling
No Drop Shadows
No Effects
Never use less than 120% Leading

OUR CORPORATE COLOURS
BRAND GUIDELINES
We were thinking that our primary colour palette consists of the Acid Green (Pantone 382) and Process Black.

We work closely with tquarly Ltd and would like to include their name on the card somewhere. I have attached images of the other brands that we work with as an idea or the small icons I have included that illustrate what we do?. I have very kindly been given permission to use any of the images off the files that I have included below, so I hope these help. I will include these below. I would be open to suggestions if it made the card more striking Can you do it?
Updates

Hi All, Just wanted to add a few thoughts but you are the guys with the creative visions (thats why are here) We are based in Wales, UK and we would be open to lots of different ideas on a theme but must be eye catching, Bold and FUN. If you can or think that the Welsh or any dragon could be put in there then go for it (its not a must have) We have also added some ideas for colour but again its over to you!! GO FOR IT ! Thanks and look forward to your visions! Owen

Hi All, Just thought I would sen through the contact details that need to be on the card. (if you want to play around with icons instead of the wording twitter, Facebook, go for it): Corvane Motion Limited Owen Pritchard Managing Director Mob: +44 (0)7582 913 406 e-mail: sales@corvanemotion.co.uk Web: Corvanemotion.co.uk twitter: @motionLetterbin Facebook: Corvane Motion Limited

```html
<!DOCTYPE html>
<html lang="en">
<head>
<meta charset="utf-8">
<title>Corvane Motion Limited – Business Card</title>
<link href="https://fonts.googleapis.com/css2?family=Arimo:wght@400;700&display=swap" rel="stylesheet">
<style>
  :root {
    --page: #e9e6e1;
    --card-white: #f7f7f5;
    --navy: #141a4e;
    --navy-deep: #0f1440;
    --gold: #b8962e;
    --gold-light: #cfae4a;
    --text-light: #ffffff;
    --tile-blue: #1769b3;
    --tile-sky: #2fb4e6;
    --tile-steel: #8fa6ba;
    --tile-deep: #0e4b8c;
    --tile-mist: #bccbd7;
    --tile-mid: #1f5fa3;
  }
  * { box-sizing: border-box; margin: 0; padding: 0; }
  html, body { width: 1200px; height: 892px; overflow: hidden; }
  body {
    background: var(--page);
    font-family: "Arimo", Arial, sans-serif;
    position: relative;
  }

  .card {
    position: absolute;
    width: 580px;
    height: 332px;
    border-radius: 4px;
    overflow: hidden;
    box-shadow: 0 6px 18px rgba(0,0,0,0.18);
  }

  /* Front */
  .card-front {
    left: 90px;
    top: 80px;
    background: var(--card-white);
    border: 4px solid var(--gold);
  }
  .brand-mark {
    position: absolute;
    left: 34px;
    top: 40px;
    display: flex;
    align-items: center;
    gap: 14px;
  }
  .brand-dot {
    width: 58px;
    height: 58px;
    border-radius: 50%;
    background: var(--navy);
    flex: none;
  }
  .brand-name {
    font-weight: 700;
    font-size: 21px;
    line-height: 1.25;
    color: var(--navy);
    width: 170px;
  }
  .info-panel {
    position: absolute;
    left: 258px;
    top: 96px;
    right: 0;
    bottom: 0;
    background: linear-gradient(160deg, var(--navy) 0%, var(--navy-deep) 100%);
    border-top: 3px solid var(--gold);
    border-left: 3px solid var(--gold);
    padding: 22px 24px 0 26px;
    color: var(--text-light);
  }
  .person-name {
    font-size: 30px;
    line-height: 1.2;
    color: var(--gold-light);
    font-weight: 400;
  }
  .person-role {
    font-size: 17px;
    line-height: 1.3;
    margin-bottom: 18px;
  }
  .contact-list { list-style: none; }
  .contact-item {
    display: flex;
    align-items: center;
    gap: 10px;
    font-size: 14px;
    line-height: 1.45;
  }
  .contact-icon {
    width: 12px;
    height: 12px;
    flex: none;
    background: var(--gold);
    border-radius: 2px;
    display: flex;
    align-items: center;
    justify-content: center;
  }

  /* Back */
  .card-back {
    left: 530px;
    top: 480px;
    display: grid;
    grid-template-columns: repeat(6, 1fr);
    grid-template-rows: repeat(3, 1fr);
    background: var(--tile-deep);
  }
  .tile { width: 100%; height: 100%; }
  .tile-blue { background: var(--tile-blue); }
  .tile-sky { background: var(--tile-sky); }
  .tile-steel { background: var(--tile-steel); }
  .tile-deep { background: var(--tile-deep); }
  .tile-mist { background: var(--tile-mist); }
  .tile-mid { background: var(--tile-mid); }
  .back-mark {
    position: absolute;
    left: 184px;
    top: 128px;
    display: flex;
    align-items: center;
    gap: 12px;
  }
  .back-dot {
    width: 40px;
    height: 40px;
    border-radius: 50%;
    background: var(--text-light);
  }
  .back-name {
    font-weight: 700;
    font-size: 30px;
    line-height: 1.2;
    color: var(--text-light);
    width: 230px;
  }
</style>
</head>
<body>

  <section class="card card-front" aria-label="Business card front">
    <div class="brand-mark">
      <span class="brand-dot"></span>
      <span class="brand-name">Corvane Motion Limited</span>
    </div>

    <div class="info-panel">
      <h1 class="person-name">Owen Pritchard</h1>
      <p class="person-role">Managing Director</p>
      <ul class="contact-list">
        <li class="contact-item"><span class="contact-icon"></span>@motionLetterbin</li>
        <li class="contact-item">
          <span class="contact-icon">
            <svg width="8" height="8" viewBox="0 0 8 8"><path d="M1.5 0.8 L3 0.8 L3.4 2.4 L2.6 3 Q3.3 4.6 5 5.4 L5.6 4.6 L7.2 5 L7.2 6.5 Q3.5 7 1 2.5 Z" fill="#141a4e"/></svg>
          </span>+44 (0)7582 913 406</li>
        <li class="contact-item">
          <span class="contact-icon">
            <svg width="8" height="8" viewBox="0 0 8 8"><circle cx="4" cy="4" r="3" fill="none" stroke="#141a4e" stroke-width="1"/><line x1="1" y1="4" x2="7" y2="4" stroke="#141a4e" stroke-width="0.8"/></svg>
          </span>Corvanemotion.co.uk</li>
        <li class="contact-item"><span class="contact-icon"></span>Corvane Motion Limited</li>
        <li class="contact-item">
          <span class="contact-icon">
            <svg width="8" height="8" viewBox="0 0 8 8"><rect x="0.6" y="1.6" width="6.8" height="4.8" fill="none" stroke="#141a4e" stroke-width="0.9"/><path d="M0.6 1.6 L4 4.4 L7.4 1.6" fill="none" stroke="#141a4e" stroke-width="0.9"/></svg>
          </span>sales@corvanemotion.co.uk</li>
      </ul>
    </div>
  </section>

  <section class="card card-back" aria-label="Business card back">
    <div class="tile tile-blue" role="img" aria-label="Treadmill icon"></div>
    <div class="tile tile-sky" role="img" aria-label="Exercise bike icon"></div>
    <div class="tile tile-blue"></div>
    <div class="tile tile-mid"></div>
    <div class="tile tile-deep"></div>
    <div class="tile tile-mid"></div>

    <div class="tile tile-deep" role="img" aria-label="Weight plate photo detail"></div>
    <div class="tile tile-steel" role="img" aria-label="Kettlebell icon"></div>
    <div class="tile tile-mid"></div>
    <div class="tile tile-deep"></div>
    <div class="tile tile-mid"></div>
    <div class="tile tile-deep"></div>

    <div class="tile tile-deep" role="img" aria-label="Skipping rope icon"></div>
    <div class="tile tile-blue" role="img" aria-label="Nutrition shake and apple icon"></div>
    <div class="tile tile-mist" role="img" aria-label="Weighing scale icon"></div>
    <div class="tile tile-blue"></div>
    <div class="tile tile-mid" role="img" aria-label="Boxing gloves icon"></div>
    <div class="tile tile-steel"></div>

    <div class="back-mark">
      <span class="back-dot"></span>
      <span class="back-name">Corvane Motion Limited</span>
    </div>
  </section>

</body>
</html>
```